Carpet cleaning company focused on high quality needs business cards

We are a growing company that just merged with another company and need to design a new business card. We do both residential as well as commercial cleaning. We do carpet, tile & grout, upholstery, hard floors, and stain & pet odor removal. We treat our customers like family and strive to achieve outstanding results with every job.

```html
<!DOCTYPE html>
<html lang="en">
<head>
<meta charset="utf-8">
<title>Ridgeway Steam Cleaning – Business Card</title>
<link href="https://fonts.googleapis.com/css2?family=Montserrat:wght@400;500;700;800&display=swap" rel="stylesheet">
<style>
  :root {
    --ink: #1a1a1a;
    --red: #e8413c;
    --blue: #1b7fc1;
    --tan: #c4a266;
    --card: #ffffff;
    --backdrop: #e4e4e6;
  }
  * { box-sizing: border-box; margin: 0; padding: 0; }
  html, body { width: 1200px; height: 900px; overflow: hidden; }
  body {
    background: var(--backdrop);
    font-family: "Montserrat", Arial, sans-serif;
    color: var(--ink);
    position: relative;
  }
  .card {
    position: absolute;
    width: 600px;
    height: 340px;
    background: var(--card);
    border-radius: 22px;
    overflow: hidden;
    box-shadow: 0 6px 18px rgba(0,0,0,.12);
  }
  .card--front { left: 300px; top: 60px; }
  .card--back  { left: 300px; top: 480px; }

  .brand {
    display: flex;
    align-items: center;
    gap: 18px;
  }
  .brand__name {
    font-weight: 800;
    color: var(--ink);
    line-height: 1;
    text-transform: uppercase;
  }
  .brand__name span { display: block; }

  /* front */
  .card--front .brand {
    position: absolute;
    left: 50%; top: 50%;
    transform: translate(-50%, -50%);
  }
  .brand__mark {
    width: 64px; height: 64px;
    background: var(--red);
    flex: none;
  }
  .card--front .brand__name { font-size: 34px; }

  /* back */
  .illustration {
    position: absolute;
    left: 0; bottom: 0;
    width: 340px; height: 340px;
  }
  .info {
    position: absolute;
    left: 370px; top: 30px;
    width: 210px;
  }
  .card--back .brand__name { font-size: 20px; }
  .person { margin-top: 16px; }
  .person__name {
    font-weight: 700;
    font-size: 22px;
    line-height: 1.15;
    color: var(--red);
  }
  .person__role {
    font-size: 12px;
    font-weight: 500;
    margin-top: 2px;
  }
  .address {
    font-size: 12px;
    line-height: 1.4;
    margin-top: 12px;
  }
  .contacts { list-style: none; margin-top: 10px; }
  .contacts li {
    display: flex; align-items: center; gap: 8px;
    font-size: 12px; line-height: 1.7;
    white-space: nowrap;
  }
  .contacts svg { width: 12px; height: 12px; fill: var(--red); flex: none; }
</style>
</head>
<body>

<section class="card card--front">
  <div class="brand">
    <div class="brand__mark"></div>
    <div class="brand__name"><span>Ridgeway</span><span>Steam</span><span>Cleaning</span></div>
  </div>
</section>

<section class="card card--back">
  <svg class="illustration" viewBox="0 0 340 340" role="img" aria-label="Cartoon mascot of a cheerful cleaner in a blue cap and shirt holding a steam wand, over a red diagonal panel">
    <defs>
      <linearGradient id="mascotTone" x1="0" y1="0" x2="1" y2="1">
        <stop offset="0" stop-color="#5a9fd0"/>
        <stop offset="1" stop-color="#c4a266"/>
      </linearGradient>
    </defs>
    <polygon points="150,340 340,150 340,340" fill="var(--red)"/>
    <polygon points="0,90 40,60 250,200 250,340 0,340" fill="url(#mascotTone)" opacity=".85"/>
  </svg>

  <div class="info">
    <div class="brand">
      <div class="brand__name"><span>Ridgeway</span><span>Steam Cleaning</span></div>
    </div>
    <div class="person">
      <div class="person__name">Daniel Porter</div>
      <div class="person__role">CEO</div>
    </div>
    <div class="address">418 Maple Grove Ave, #112<br>Fairview, OH 43210</div>
    <ul class="contacts">
      <li><svg viewBox="0 0 12 12"><path d="M2.5 0.5l2 2.5-1 1.2c.6 1.4 1.9 2.7 3.3 3.3l1.2-1 2.5 2-1 2C5 10.5 1.5 7 .5 1.5z"/></svg>555 310-4472</li>
      <li><svg viewBox="0 0 12 12"><path d="M3 0h6v12H3zM4 1.5v8h4v-8z"/></svg>555 310-4472</li>
      <li><svg viewBox="0 0 12 12"><path d="M0 2h12v8H0zM1 3l5 3.5L11 3z"/></svg>info@ridgewaysteam.com</li>
      <li><svg viewBox="0 0 12 12"><circle cx="6" cy="6" r="5.5"/><path d="M0.5 6h11M6 .5v11" stroke="#fff" stroke-width=".8"/></svg>www.ridgewaysteam.com</li>
    </ul>
  </div>
</section>

</body>
</html>
```